Website for IT Security Company in Austria with small and medium business customer base

I own a one man IT security company with a customer small to medium business customer base and need a professional looking website that contains the following information:
- Home page: About the company....
- Services: The services that I offer. It would be nice to have icons if possible (e.g Active Directory icon, digital certificate icon, ...) but this is not a must have.
- About me
- Blog: This is not a must have. It would be ok to just link it to an external blog.
- Impressum
- Contact: No form, just telephone number and e-mail address
- Anything else that you think is necessary for a professional appearance
Also I attached the company design. I do have all source files for the logo if required.

Target Market(s)

Small and medium business of all branches located in Austria

Industry/Entity Type

Cyber Security

Coding

Coded - Design and coding required

Number of Pages Required

5+ page

Font styles to use
Serif
Sans Serif
Other font styles liked:
• Bitsumishi, Bankgothic

Colors

Designer to choose only greyscale colors for use in the design.

Requirements
Must have
• The website must be a mobile-first design.
The design should not be too colorful or playful.
The logo should be used as much as possible
Navigation bar with multi drop-down menu for the services that I offer.
Example:
Services
-> Implementations
-> Implementation Service A
-> Implementation Service B
-> Security Audit
-> Audit A
-> Audit B
Maybe you could have service cards that describe the services briefly and on click redirect to the site that describes the service in detail.
End of example
Logo
contact
impressum
services that I offer
about me
about the company
Nice to have
• Icons would be nice (e.g. house for homepage, letter for contact, ...)
Also for the services I offer icons would be nice (Active Directory, digtial certificates, hacking, security auditing)
For the fonts I have only sugested Bitsumishi and Bankgothic as they are part of my logo. No sure if you feel they make sense as part of the website
Should not have
• forms.
I want to the site to be made as easy as possible (HTML5, CSS, javascript/php/.net)
I do not want a wordpress template or suchlike.

```html
<!DOCTYPE html>
<html lang="en">
<head>
<meta charset="utf-8">
<title>Basalt Guard IT Security</title>
<link rel="stylesheet" href="https://fonts.googleapis.com/css2?family=Orbitron:wght@600;700;800&family=Lato:ital,wght@0,400;0,700;1,400&display=swap">
<style>
:root{
  --ink:#1e1e1f;
  --ink-soft:#3a3a3c;
  --text:#444;
  --muted:#777;
  --line:#cfcfcf;
  --paper:#ffffff;
  --mist:#eeeeee;
  --dark:#222224;
  --accent:#9c9c9c;
  --display:'Orbitron',sans-serif;
  --body:'Lato',sans-serif;
}
*{box-sizing:border-box;margin:0;padding:0}
html,body{width:1200px;height:3629px;overflow:hidden;background:var(--paper)}
.page{position:relative;width:1200px;height:3629px;overflow:hidden;font-family:var(--body);color:var(--text)}
.display{font-family:var(--display);font-weight:700;letter-spacing:2px;color:var(--ink);text-transform:uppercase}

/* header */
.site-header{position:absolute;top:0;left:0;width:1200px;height:112px;background:var(--paper);z-index:5}
.brand-tab{position:absolute;left:58px;top:0;width:290px;height:152px;background:var(--paper);z-index:6;clip-path:polygon(0 0,100% 0,100% 100%,3% 100%)}
.brand{position:absolute;display:flex;align-items:center;gap:10px;font-family:var(--display);font-weight:800;color:var(--ink);letter-spacing:1px;white-space:nowrap}
.brand-mark{width:22px;height:22px;background:var(--ink);display:block}
.header-brand{left:58px;width:290px;top:0;height:152px;justify-content:center;font-size:21px;z-index:7}
.nav{position:absolute;top:52px;left:434px;font-family:var(--display);font-weight:700;font-size:13px;letter-spacing:1px;color:var(--ink-soft)}
.nav a{color:inherit;text-decoration:none;position:absolute;white-space:nowrap}

/* hero */
.hero{position:absolute;top:112px;left:0;width:1200px;height:700px;background:radial-gradient(circle at 75% 35%,#6a6a6c 0%,#3a3a3c 35%,#1c1c1e 70%,#0e0e0f 100%)}
.hero-title{position:absolute;left:73px;top:218px;font-family:var(--display);font-weight:800;font-size:46px;letter-spacing:4px;color:#fff}
.hero-sub{position:absolute;left:86px;top:280px;font-family:var(--display);font-weight:700;font-size:33px;letter-spacing:9px;color:#fff}
.hero-text{position:absolute;left:74px;top:334px;width:500px;font-size:20px;line-height:29px;color:#fff}
.dots{position:absolute;left:75px;top:504px;display:flex;gap:10px}
.dots span{width:10px;height:10px;border-radius:50%;background:#fff}
.dots span:first-child{background:var(--accent)}
.hero-wave{position:absolute;left:0;top:680px}

/* welcome */
.welcome-art{position:absolute;left:75px;top:876px;width:502px;height:434px;background:linear-gradient(135deg,#2c2c2e 0%,#777 45%,#1e1e20 100%);clip-path:polygon(25% 0,75% 0,100% 50%,75% 100%,25% 100%,0 50%)}
.welcome-title{position:absolute;left:613px;top:904px;font-size:24px;line-height:34px}
.welcome-copy{position:absolute;left:613px;top:986px;width:520px;font-size:14.5px;line-height:30.5px;color:var(--text)}
.btn{position:absolute;left:613px;top:1232px;width:208px;height:45px;border-radius:23px;background:var(--ink-soft);color:#fff;font-family:var(--display);font-weight:600;font-size:14px;letter-spacing:4px;display:flex;align-items:center;justify-content:center}

/* services */
.services{position:absolute;left:0;top:1390px;width:1200px;height:681px;background:linear-gradient(160deg,#2a2a2c 0%,#18181a 55%,#222 100%)}
.services-wave{position:absolute;left:0;top:1388px}
.services-title{position:absolute;left:0;width:1200px;top:1534px;text-align:center;color:#fff;font-size:24px;letter-spacing:3px}
.card{position:absolute;width:254px;height:325px;background:var(--paper);border-radius:20px;text-align:center;padding:0 12px}
.card svg{display:block;margin:0 auto}
.card h3{font-family:var(--display);font-weight:800;font-size:20px;letter-spacing:1.5px;color:var(--ink);margin:18px 0 10px}
.card p{font-size:13.5px;line-height:26px;color:#555}

/* clients */
.section-title{position:absolute;left:0;width:1200px;text-align:center;font-size:24px;letter-spacing:3px}
.client{position:absolute;top:2197px;width:165px;height:69px;border:2px solid var(--line);display:flex;align-items:center;justify-content:center;gap:8px;font-weight:700;font-size:20px;color:var(--ink-soft)}
.client i{width:16px;height:16px;border-radius:50%;background:var(--ink-soft);display:block}

/* testimonials */
.testimonials{position:absolute;left:0;top:2344px;width:1200px;height:499px;background:var(--mist)}
.quote-card{position:absolute;background:var(--paper);border-radius:18px;box-shadow:0 4px 14px rgba(0,0,0,.08);text-align:center}
.quote-badge{position:absolute;border-radius:50%;background:var(--paper);box-shadow:0 2px 8px rgba(0,0,0,.15);display:flex;align-items:center;justify-content:center;font-family:Georgia,serif;font-weight:700;color:var(--ink)}
.person{position:absolute;display:flex;align-items:center;gap:14px;text-align:left;color:var(--ink)}
.avatar{border-radius:50%;background:var(--ink);display:flex;align-items:center;justify-content:center}
.arrow{position:absolute;top:2629px;width:28px;height:28px;border-radius:50%;background:#a8a8a8;display:flex;align-items:center;justify-content:center}

/* contact */
.contact-brand{left:0;width:1200px;top:3060px;justify-content:center;font-size:30px}
.contact-line{position:absolute;left:0;width:1200px;top:3154px;display:flex;justify-content:center;align-items:center;gap:26px;font-family:var(--display);font-weight:700;font-size:20px;color:var(--ink);letter-spacing:1px}
.contact-line span{display:flex;align-items:center;gap:12px}

/* footer */
.footer{position:absolute;left:0;top:3250px;width:1200px;height:379px;background:var(--dark)}
.footer-curve{position:absolute;left:0;top:3230px}
.f-col{position:absolute;top:3340px}
.f-col h4{font-weight:700;font-size:18px;color:#fff;margin-bottom:8px}
.f-col p,.f-col li{font-size:13px;line-height:25px;color:#ddd;list-style:none}
.f-col.links li{line-height:23px}
.signup{display:flex;margin-top:8px;width:240px;height:36px;border-radius:18px;overflow:hidden;background:#fff}
.signup span{flex:1;font-size:12px;color:#888;padding:10px 18px}
.signup b{width:42px;background:var(--ink);color:#fff;font-size:13px;display:flex;align-items:center;justify-content:center}
.social{display:flex;gap:20px;margin-top:10px}
.social i{width:14px;height:14px;border-radius:50%;background:#eee;display:block}
.f-rule{position:absolute;left:75px;top:3574px;width:1050px;height:1px;background:#555}
.copyright{position:absolute;left:0;width:1200px;top:3590px;text-align:center;font-size:12px;color:#bbb}
</style>
</head>
<body>
<div class="page">

  <header class="site-header">
    <nav class="nav">
      <a style="left:0;color:var(--ink)">HOME</a>
      <a style="left:89px">ABOUT US</a>
      <a style="left:228px">SERVICES</a>
      <a style="left:356px">SOLUTION</a>
      <a style="left:484px">BLOG</a>
      <a style="left:572px">CONTACT US</a>
    </nav>
  </header>
  <div class="brand-tab"></div>
  <div class="brand header-brand"><span class="brand-mark"></span>BASALT GUARD</div>

  <section class="hero" role="img" aria-label="Photo of a security specialist working on a laptop in a dark server room">
    <h1 class="hero-title">BASALT GUARD</h1>
    <div class="hero-sub">IT SECURITY</div>
    <p class="hero-text">Pellentesque habitant morbi tristique senectus et netus et malesuada fames.</p>
    <div class="dots"><span></span><span></span><span></span><span></span></div>
  </section>
  <svg class="hero-wave" width="1200" height="140" viewBox="0 0 1200 140" aria-hidden="true">
    <path d="M0 35 C120 10 240 20 360 55 C520 105 650 115 820 95 C960 80 1080 70 1200 110 L1200 140 L0 140Z" fill="#1a1a1a"/>
    <path d="M0 40 C120 16 240 26 360 61 C520 111 650 118 820 99 C960 85 1080 78 1200 122 L1200 140 L0 140Z" fill="#fff"/>
  </svg>

  <div class="welcome-art" role="img" aria-label="Hexagonal digital illustration of a glowing key and circuitry"></div>
  <h2 class="display welcome-title">Welcome to<br>Basalt Guard IT Security</h2>
  <p class="welcome-copy">Lorem ipsum dolor sit amet, consectetur adipiscing elit. Vestibulum at risus vitae metus fringilla tristique. Nulla facilisi. Mauris interdum faucibus risus non lacinia. Sed vulputate neque eget metus porttitor, ac consectetur felis porta natoque penatibus et magnis dis parturient montes, nascetur ridiculus mus. Sed ut placerat sapien. Cras et tristique tellus, non scelerisque leo. Ut bibendum mauris vitae ipsum imperdiet ultrices.</p>
  <div class="btn">READ MORE</div>

  <section class="services" role="img" aria-label="Dark photo of a laptop screen showing a security message"></section>
  <svg class="services-wave" width="1200" height="104" viewBox="0 0 1200 104" aria-hidden="true">
    <path d="M0 0 H1200 V5 C1140 10 1100 92 1010 96 C900 100 800 22 640 12 C480 2 350 80 200 96 C120 103 60 100 0 100 Z" fill="#fff"/>
  </svg>
  <h2 class="display services-title">Our Services</h2>

  <article class="card" style="left:74px;top:1672px">
    <svg width="66" height="50" viewBox="0 0 66 50" style="margin-top:42px" fill="none" stroke="#222" stroke-width="3"><rect x="8" y="3" width="50" height="34" rx="3"/><path d="M2 44 H64" stroke-width="5"/></svg>
    <h3>VESTIBULUM</h3>
    <p>Donec in tortor hendrerit, bibendum nibh in, euismod massa. Lorem ipsum dolor sit amet, consectetur adipiscing elit nec diam eu ligula imperdiet..</p>
  </article>
  <article class="card" style="left:340px;top:1610px">
    <svg width="60" height="68" viewBox="0 0 60 68" style="margin-top:26px" fill="none" stroke="#222" stroke-width="3"><path d="M16 30 V18 a14 14 0 0 1 28 0 V30"/><rect x="4" y="30" width="52" height="35" rx="5"/></svg>
    <h3>VESTIBULUM</h3>
    <p>Donec in tortor hendrerit, bibendum nibh in, euismod massa. Lorem ipsum dolor sit amet, consectetur adipiscing elit nec diam eu ligula imperdiet..</p>
  </article>
  <article class="card" style="left:606px;top:1672px">
    <svg width="68" height="56" viewBox="0 0 68 56" style="margin-top:40px" fill="none" stroke="#222" stroke-width="3"><path d="M28 4 C14 4 4 12 4 22 C4 28 8 33 13 36 L10 46 L22 39 C24 40 26 40 28 40 C42 40 52 32 52 22 C52 12 42 4 28 4Z"/><path d="M55 18 C61 22 64 27 64 32 C64 37 61 41 57 44 L60 53 L49 47 C44 48 38 47 34 44"/></svg>
    <h3>VESTIBULUM</h3>
    <p>Donec in tortor hendrerit, bibendum nibh in, euismod massa. Lorem ipsum dolor sit amet, consectetur adipiscing elit nec diam eu ligula imperdiet..</p>
  </article>
  <article class="card" style="left:873px;top:1610px">
    <svg width="84" height="64" viewBox="0 0 84 64" style="margin-top:26px" fill="none" stroke="#222" stroke-width="3"><circle cx="28" cy="32" r="18" stroke-dasharray="7 4"/><circle cx="28" cy="32" r="7"/><circle cx="64" cy="16" r="10" stroke-dasharray="5 3"/><circle cx="64" cy="16" r="3.5"/><circle cx="64" cy="48" r="10" stroke-dasharray="5 3"/><circle cx="64" cy="48" r="3.5"/></svg>
    <h3>VESTIBULUM</h3>
    <p>Donec in tortor hendrerit, bibendum nibh in, euismod massa. Lorem ipsum dolor sit amet, consectetur adipiscing elit nec diam eu ligula imperdiet..</p>
  </article>

  <h2 class="display section-title" style="top:2135px">Our Clients</h2>
  <div class="client" style="left:75px"><i></i>Nordvale</div>
  <div class="client" style="left:252px"><i></i>Quillon</div>
  <div class="client" style="left:429px"><i></i>Arbento</div>
  <div class="client" style="left:606px"><i></i>Lumetra</div>
  <div class="client" style="left:784px"><i></i>Kestrix</div>
  <div class="client" style="left:962px"><i></i>Ostwind</div>

  <section class="testimonials"></section>
  <h2 class="display section-title" style="top:2418px">Customer Testimonials</h2>

  <div class="quote-card" style="left:-60px;top:2543px;width:323px;height:194px;opacity:.85">
    <p style="font-style:italic;font-size:11px;line-height:21px;color:#888;padding:38px 16px 0 60px;text-align:left">Lorem ipsum dolor sit amet, consectetur adipiscing elit. Pellentesque odio augue, nisl sed, maximus viverra leo maximus nunc in dolor, facilisis non congue imperdiet.."</p>
    <div class="person" style="left:56px;top:125px"><span class="avatar" style="width:42px;height:42px"><svg width="16" height="18" viewBox="0 0 16 18" fill="#fff"><circle cx="8" cy="5" r="4"/><path d="M0 18 C0 11 16 11 16 18Z"/></svg></span><span style="font-size:12px;line-height:17px"><b>Name Heading</b><br><i>Location</i></span></div>
  </div>
  <div class="quote-badge" style="left:59px;top:2522px;width:46px;height:46px;font-size:24px">&#8221;</div>

  <div class="quote-card" style="left:946px;top:2543px;width:323px;height:194px;opacity:.85">
    <p style="font-style:italic;font-size:11px;line-height:21px;color:#888;padding:38px 16px 0 16px">" Lorem ipsum dolor sit amet, consectetur adipiscing augue, condimentum vel nisl sed, maximus viverra mattis iaculis dolor, facilisis non congue</p>
    <div class="person" style="left:136px;top:125px"><span class="avatar" style="width:48px;height:48px"><svg width="18" height="20" viewBox="0 0 16 18" fill="#fff"><circle cx="8" cy="5" r="4"/><path d="M0 18 C0 11 16 11 16 18Z"/></svg></span><span style="font-size:12px;line-height:17px"><b>Name Heading</b><br><i>Location</i></span></div>
  </div>
  <div class="quote-badge" style="left:1126px;top:2522px;width:46px;height:46px;font-size:24px">&#8221;</div>

  <div class="arrow" style="left:290px"><svg width="14" height="14" viewBox="0 0 14 14" fill="none" stroke="#fff" stroke-width="2.5"><path d="M13 7H2M7 2L2 7L7 12"/></svg></div>
  <div class="arrow" style="left:890px"><svg width="14" height="14" viewBox="0 0 14 14" fill="none" stroke="#fff" stroke-width="2.5"><path d="M1 7H12M7 2L12 7L7 12"/></svg></div>

  <div class="quote-card" style="left:346px;top:2520px;width:515px;height:245px">
    <p style="font-size:14.5px;line-height:27px;color:#444;padding:44px 18px 0">“ Lorem ipsum dolor sit amet, consectetur adipiscing elit odio augue, condimentum vel nisl sed, maximus viverra leo maximus nunc in mattis iaculis dolor, facilisis non congue imperdiet.”</p>
    <div class="person" style="left:172px;top:153px"><span class="avatar" style="width:58px;height:58px"><svg width="22" height="24" viewBox="0 0 16 18" fill="#fff"><circle cx="8" cy="5" r="4"/><path d="M0 18 C0 11 16 11 16 18Z"/></svg></span><span style="font-size:14px;line-height:21px;font-weight:700">Name Heading<br>Location</span></div>
  </div>
  <div class="quote-badge" style="left:575px;top:2491px;width:56px;height:56px;font-size:30px">&#8221;</div>

  <h2 class="display section-title" style="top:2921px">Contact Us</h2>
  <div class="brand contact-brand"><span class="brand-mark" style="width:30px;height:30px"></span>BASALT GUARD</div>
  <div class="contact-line">
    <span><svg width="24" height="24" viewBox="0 0 24 24" fill="#1e1e1f"><path d="M6.6 2.5 L9.5 6.5 L7.6 9.2 C8.8 11.8 11.2 14.4 14.2 15.8 L16.8 13.9 L21 16.8 L19.2 20.6 C12 21 3 12 3.4 4.3Z"/></svg>1-800-555-0142</span>
    <span style="font-family:var(--body);font-weight:400">|</span>
    <span><svg width="26" height="20" viewBox="0 0 26 20" fill="#1e1e1f"><path d="M1 2H25V4L13 11L1 4Z"/><path d="M1 6L13 13L25 6V18H1Z"/></svg>INFO@COMPANYNAME.COM</span>
  </div>

  <svg class="footer-curve" width="1200" height="40" viewBox="0 0 1200 40" aria-hidden="true"><path d="M0 28 C300 34 700 32 1200 0 V40 H0Z" fill="#222224"/></svg>
  <footer class="footer"></footer>
  <div class="f-col" style="left:75px;width:250px">
    <h4>ABOUT US</h4>
    <p>Lorem ipsum dolor sit amet, consectetur adipiscing elit nunc ac fringilla lectus. Nam faucibus, massa vel hendrerit euismod, diam erat tincidunt felis..</p>
  </div>
  <div class="f-col links" style="left:382px">
    <h4>QUICK LINKS</h4>
    <ul><li>Home</li><li>About Us</li><li>About Me</li><li>Services</li><li>Solution</li><li>Blog</li><li>Contact Us</li><li>Impressum</li></ul>
  </div>
  <div class="f-col" style="left:619px">
    <h4>SERVICES</h4>
    <ul><li>Sed ut perspiciatis</li><li>Unde omnis iste natus</li><li>Error sit voluptatem</li><li>Accusantium</li><li>Nemo enim ipsam</li></ul>
  </div>
  <div class="f-col" style="left:884px">
    <h4>EMAIL SIGN UP</h4>
    <div class="signup"><span>Enter Email Address</span><b>GO</b></div>
    <h4 style="margin-top:30px">FOLLOW US</h4>
    <div class="social" aria-label="Social media links"><i></i><i></i><i></i><i></i><i></i></div>
  </div>
  <div class="f-rule"></div>
  <p class="copyright">Copyright © 2021. Company Name . All Right Reserved &nbsp;|&nbsp; Impressum</p>

</div>
</body>
</html>
```